Icons/images for company values

We have five company values, we have a new logo and a new look. I would like drawn images for each value that are in keeping with our look and feel.

Target Market(s)

internal/staff

Industry/Entity Type

media compliance

Requirements
Must have
• colours aligned with logo.

```html
<!DOCTYPE html>
<html lang="en">
<head>
<meta charset="utf-8">
<title>Norvane Values 2023</title>
<link href="https://fonts.googleapis.com/css2?family=Anton&family=Barlow+Semi+Condensed:wght@700&family=Poppins:wght@400&display=swap" rel="stylesheet">
<style>
  :root {
    --page: #ffffff;
    --navy: #136b8f;
    --brand-blue: #1b80b9;
    --teal-head: #3cbdb0;
    --ink: #1e1e1e;
    --band: #e4e4dc;
    --lime: #d7e35a;
  }
  * { margin: 0; padding: 0; box-sizing: border-box; }
  html, body { width: 1200px; height: 800px; overflow: hidden; background: var(--page); }
  .canvas { position: relative; width: 1200px; height: 800px; background: var(--page); overflow: hidden; }
  .graphics { position: absolute; left: 0; top: 0; }

  .brand-name {
    position: absolute; left: 113px; top: 90px; width: 190px;
    font-family: "Poppins", sans-serif; font-weight: 400; font-size: 30px;
    letter-spacing: 6px; color: var(--brand-blue);
  }
  .title-frame {
    position: absolute; left: 333px; top: 28px; width: 754px; height: 146px;
    border: 2px solid var(--navy); border-top-color: var(--lime);
    display: flex; align-items: center; justify-content: center;
  }
  .title-band { position: absolute; left: 1087px; top: 28px; width: 113px; height: 146px; background: var(--band); }
  .title {
    font-family: "Anton", sans-serif; font-size: 124px; line-height: 1;
    color: var(--navy); letter-spacing: 2px; font-weight: 400;
  }

  .value { position: absolute; width: 360px; margin-left: -180px; text-align: center; }
  .value-title {
    font-family: "Barlow Semi Condensed", sans-serif; font-weight: 700;
    font-size: 18px; line-height: 20px; color: var(--teal-head); letter-spacing: 0.3px;
  }
  .value-text {
    font-family: "Poppins", sans-serif; font-size: 12.5px; line-height: 15px;
    color: var(--ink); margin-top: 7px;
  }
  .value-wide { width: 480px; margin-left: -240px; }

  .open-honest { left: 217px; top: 362px; }
  .faster-together { left: 978px; top: 362px; }
  .copyright-leaders { left: 217px; top: 566px; }
  .things-done { left: 978px; top: 566px; }
  .diverse-perspectives { left: 600px; top: 681px; }
</style>
</head>
<body>
<main class="canvas">
  <svg class="graphics" width="1200" height="800" viewBox="0 0 1200 800">
    <defs>
      <linearGradient id="ring" x1="0" y1="0" x2="0" y2="1">
        <stop offset="0" stop-color="#d7e35a"/>
        <stop offset="0.45" stop-color="#17a58c"/>
        <stop offset="1" stop-color="#1470ad"/>
      </linearGradient>
      <linearGradient id="core" x1="0" y1="0" x2="0" y2="1">
        <stop offset="0" stop-color="#b9e35c"/>
        <stop offset="0.45" stop-color="#22b39b"/>
        <stop offset="1" stop-color="#1672b6"/>
      </linearGradient>
      <linearGradient id="wire" x1="0" y1="0" x2="0" y2="1">
        <stop offset="0" stop-color="#d7e35a"/>
        <stop offset="1" stop-color="#1470ad"/>
      </linearGradient>
      <linearGradient id="rocket" x1="0" y1="0" x2="0" y2="1">
        <stop offset="0" stop-color="#f2f2f2"/>
        <stop offset="0.55" stop-color="#f2a5bd"/>
        <stop offset="1" stop-color="#fbe65a"/>
      </linearGradient>
      <g id="badge">
        <circle r="50" fill="url(#ring)"/>
        <circle r="41" fill="#ffffff"/>
        <circle r="37" fill="url(#core)"/>
      </g>
    </defs>

    <g class="connectors" stroke="#1a86a0" stroke-width="2">
      <line x1="300" y1="296" x2="520" y2="296"/>
      <line x1="682" y1="296" x2="880" y2="296"/>
      <line x1="300" y1="500" x2="540" y2="500"/>
      <line x1="640" y1="500" x2="880" y2="500"/>
      <line x1="600" y1="535" x2="600" y2="559"/>
    </g>
    <g class="nodes" fill="url(#wire)">
      <circle cx="300" cy="296" r="7"/>
      <circle cx="880" cy="296" r="7"/>
      <circle cx="300" cy="500" r="7"/>
      <circle cx="880" cy="500" r="7"/>
      <circle cx="600" cy="559" r="7"/>
    </g>

    <rect class="rocket-art" x="470" y="193" width="260" height="342" rx="40" fill="url(#rocket)"
          role="img" aria-label="Illustration of a rocket launching with a flame trail"/>

    <g transform="translate(210 299)">
      <use href="#badge"/>
      <path d="M0 14 C-18 2 -20 -12 -10 -16 C-5 -18 -1 -14 0 -10 C1 -14 5 -18 10 -16 C20 -12 18 2 0 14Z" fill="#fff"/>
    </g>
    <g transform="translate(971 299)">
      <use href="#badge"/>
      <g fill="none" stroke="#fff" stroke-width="3">
        <circle cx="3" cy="2" r="13"/>
        <path d="M3 2 V-7 M3 2 H10"/>
        <path d="M-20 -2 H-13 M-22 4 H-12 M-18 10 H-12"/>
      </g>
      <rect x="-1" y="-17" width="8" height="4" fill="#fff"/>
    </g>
    <g transform="translate(210 505)">
      <use href="#badge"/>
      <circle cx="-4" cy="-10" r="8" fill="#fff"/>
      <path d="M-18 16 C-18 2 -10 -1 -4 -1 C2 -1 8 1 10 6 L10 16Z" fill="#fff"/>
      <circle cx="11" cy="8" r="9" fill="#fff"/>
      <path d="M11 2 L12.8 6 L17 6.3 L13.8 9 L14.8 13 L11 10.8 L7.2 13 L8.2 9 L5 6.3 L9.2 6Z" fill="#1a86a0"/>
    </g>
    <g transform="translate(971 505)">
      <use href="#badge"/>
      <g fill="#fff">
        <rect x="-18" y="6" width="6" height="12"/>
        <rect x="-10" y="0" width="6" height="18"/>
        <rect x="-2" y="-6" width="6" height="24"/>
        <rect x="6" y="-12" width="6" height="30"/>
        <circle cx="8" cy="-14" r="7"/>
      </g>
    </g>
    <g transform="translate(600 620)">
      <use href="#badge"/>
      <g fill="#fff">
        <circle cx="-10" cy="-12" r="5"/>
        <path d="M10 -18 L16 -8 H4Z"/>
        <circle cx="0" cy="-2" r="5"/>
        <path d="M-8 10 C-8 4 -4 3 0 3 C4 3 8 4 8 10Z"/>
        <path d="M-12 6 L-6 12 L-12 18 L-18 12Z"/>
        <rect x="8" y="8" width="10" height="10"/>
      </g>
    </g>
  </svg>

  <div class="brand-name">NORVANE</div>
  <div class="title-frame"><h1 class="title">VALUES 2023</h1></div>
  <div class="title-band"></div>

  <section class="value open-honest">
    <h2 class="value-title">WE'RE OPEN AND HONEST</h2>
    <p class="value-text">Sharing information helps us achieve the best<br>outcomes for our teams and business.<br>We value open, honest, &amp; clear communication.</p>
  </section>
  <section class="value faster-together">
    <h2 class="value-title">WE GET THERE FASTER, TOGETHER</h2>
    <p class="value-text">Collaboration is at the heart of what we do,<br>no matter our team</p>
  </section>
  <section class="value copyright-leaders">
    <h2 class="value-title">WE ARE LEADERS IN COPYRIGHT AND<br>INTELLECTUAL PROPERTY</h2>
    <p class="value-text">Leading the conversation in audio-visual<br>copyright compliance and advocating for the<br>protection of intellectual property globally.</p>
  </section>
  <section class="value things-done">
    <h2 class="value-title">WE GET THINGS DONE</h2>
    <p class="value-text">We grow through capability, focus and hard work.<br>We believe small steps compound to big results.</p>
  </section>
  <section class="value value-wide diverse-perspectives">
    <h2 class="value-title">DIVERSE PERSPECTIVES<br>BUILD BETTER OUTCOMES</h2>
    <p class="value-text">We value diversity, inclusion, respect and trust within our teams.<br>We are building a truly global organisation.</p>
  </section>
</main>
</body>
</html>
```